Fresh, modern, fun business card for pediatric dental practice

Need a business card for fresh, modern, fun pediatric dental practice

Clean look that matches our website's font and colors

We prefer the look of curved corners on business cards

Target Market(s)

parents (mothers) of young children, professionals, mid-high class

Industry/Entity Type

Dental

Contact Information for Business Card

Maplebrook Pediatric Dentistry
482 Quarry Lane
Suite 517
Ashgrove, PA 17999
717.555.0193
www.maplebrookkidsdental.example

Mei-Ran Tsai, DMD
Corinne Walbeck, DMD
(we are working on our email address, but we would like that on the card as well)

Font styles to use
Sans Serif

Requirements
Must have
• All info; we would also like to make cards for individual staff members
• colors from our website and color palatte, attatched
• use same font and design as website for branding
Nice to have
• clean, simple card that has a pop of color
• we would like to see a few designs with our tag line "where smiles get brighter"
• we are not sure if we want to have it on there or not
• we would like to see a few designs incorporating the ribbon graphic on our website where the word WELCOME is

```html
<!DOCTYPE html>
<html lang="en">
<head>
<meta charset="utf-8">
<title>Maplebrook Pediatric Dentistry – Business Card</title>
<link rel="stylesheet" href="https://fonts.googleapis.com/css2?family=Ubuntu:wght@500&family=Roboto:wght@400&family=Roboto+Condensed:wght@500&display=swap">
<style>
  :root {
    --backdrop: #2b2b2c;
    --card-dark: #1c1d1f;
    --card-light: #f3f3f3;
    --sun-yellow: #f6b827;
    --ink-grey: #4d4d4d;
    --white: #ffffff;
  }
  * { margin: 0; padding: 0; box-sizing: border-box; }
  html, body { width: 1200px; height: 960px; overflow: hidden; }
  body {
    position: relative;
    background: var(--backdrop);
    font-family: "Roboto", Arial, sans-serif;
  }
  .card {
    position: absolute;
    left: 320px;
    width: 600px;
    height: 342px;
    border-radius: 22px;
  }
  .card--back { top: 110px; background: var(--card-dark); }
  .card--front { top: 493px; background: var(--card-light); }

  .back-brand {
    position: absolute;
    left: 0; right: 0; top: 112px;
    text-align: center;
  }
  .back-brand__name {
    font-family: "Ubuntu", Arial, sans-serif;
    font-weight: 500;
    font-size: 44px;
    line-height: 48px;
    color: var(--sun-yellow);
  }
  .back-brand__web {
    margin-top: 12px;
    font-size: 14px;
    letter-spacing: 2.6px;
    color: var(--white);
  }

  .front-brand {
    position: absolute;
    left: 62px; top: 102px;
    font-family: "Ubuntu", Arial, sans-serif;
    font-weight: 500;
    font-size: 28px;
    line-height: 31px;
    color: var(--sun-yellow);
  }
  .doctors {
    position: absolute;
    left: 62px; top: 192px;
    font-family: "Roboto Condensed", Arial, sans-serif;
    font-weight: 500;
    font-size: 20px;
    line-height: 25px;
    color: var(--sun-yellow);
    text-transform: uppercase;
  }
  .contact {
    position: absolute;
    left: 62px; top: 250px;
    list-style: none;
    font-size: 14px;
    line-height: 20px;
    color: var(--ink-grey);
  }
  .contact li { display: flex; align-items: center; gap: 6px; }
  .contact svg { width: 13px; height: 13px; fill: var(--sun-yellow); }
  .address {
    position: absolute;
    left: 324px; top: 215px;
    font-style: normal;
    font-size: 14px;
    line-height: 18px;
    color: var(--ink-grey);
  }
</style>
</head>
<body>
  <section class="card card--back">
    <div class="back-brand">
      <p class="back-brand__name">Maplebrook<br>Pediatric Dentistry</p>
      <p class="back-brand__web">www.maplebrookkidsdental.example</p>
    </div>
  </section>

  <section class="card card--front">
    <p class="front-brand">Maplebrook<br>Pediatric Dentistry</p>
    <p class="doctors">Mei-Ran Tsai, DMD<br>Corinne Walbeck, DMD</p>
    <ul class="contact">
      <li>
        <svg viewBox="0 0 24 24" aria-hidden="true"><path d="M6.6 10.8a15.1 15.1 0 0 0 6.6 6.6l2.2-2.2c.3-.3.7-.4 1-.2 1.1.4 2.3.6 3.6.6.6 0 1 .4 1 1V20c0 .6-.4 1-1 1C10.6 21 3 13.4 3 4c0-.6.4-1 1-1h3.5c.6 0 1 .4 1 1 0 1.3.2 2.5.6 3.6.1.3 0 .7-.2 1z"/></svg>
        717.555.0193
      </li>
      <li>
        <svg viewBox="0 0 24 24" aria-hidden="true"><circle cx="12" cy="12" r="10"/><path d="M2 12h20M12 2c3 3 3 17 0 20M12 2c-3 3-3 17 0 20" stroke="#f3f3f3" stroke-width="1.6" fill="none"/></svg>
        maplebrookkidsdental.example
      </li>
    </ul>
    <address class="address">
      Maplebrook Pediatric Dentistry<br>
      482 Quarry Lane<br>
      Suite 517<br>
      Ashgrove, PA 17999
    </address>
  </section>
</body>
</html>
```